New Business Card Design Project LORVANTI-Italy

we are LORVANTI-Italy
our company in the market for 3 years we are luxury cosmetic company and its about time for a facelift :)
i will like to have elegant luxurious and unique business card
that will give the person that get it a unique, luxurious and elegant impression
I'm VERY OPEN FOR NEW IDEAS , even duo i add a few files of things that i see on line and i like them

i add my logo as well
my website is LORVANTI.COM
(if you would like to see the main style that we have)

Target Market(s)

adult that have money :)

Industry/Entity Type

Business

Contact Information for Business Card

Name - Dario Lorvanti
Position - CEO and CO Founder
address - 4817 E Halvern
telephone - 555-384-1926
email - dario@lorvanti.com
fax - 555-384-1926
website - LORVANTI.COM

Colors
000000
959595
fbee3e
ffffff

Requirements
Must have
• big logo in GOLD color
• elegant look
• impressive
Nice to have
• not must but maybe classy pattern background
• not must but maybe emblem
• maybe clear plastic business card
Should not have
• colors
• images

```html
<!DOCTYPE html>
<html lang="en">
<head>
<meta charset="utf-8">
<title>LORVANTI-Italy Business Card</title>
<link href="https://fonts.googleapis.com/css2?family=Crimson+Text:wght@400;600&display=swap" rel="stylesheet">
<style>
  :root {
    --stage: #262626;
    --card: #121212;
    --card-edge: #1c1c1c;
    --gold: #d9b23a;
    --silver: #959595;
    --white: #f2f2f2;
  }
  * { margin: 0; padding: 0; box-sizing: border-box; }
  html, body { width: 1200px; height: 833px; overflow: hidden; }
  body {
    background: var(--stage);
    font-family: "Crimson Text", Georgia, serif;
    position: relative;
  }
  .card {
    position: absolute;
    top: 262px;
    width: 540px;
    height: 309px;
    background: var(--card);
    border: 1px solid var(--card-edge);
    box-shadow: 0 12px 30px rgba(0,0,0,.5);
  }
  .card--front { left: 30px; }
  .card--back { left: 630px; }

  /* front */
  .front-mark {
    position: absolute;
    left: 50%; top: 50%;
    transform: translate(-50%, -50%);
    display: flex; flex-direction: column; align-items: center; gap: 12px;
  }
  .front-mark .mark-circle {
    width: 70px; height: 70px; border-radius: 50%;
    border: 3px solid var(--silver);
  }
  .front-mark .brand-name {
    color: var(--silver); font-size: 26px; font-weight: 400; letter-spacing: 3px;
  }

  /* back */
  .brand-block {
    position: absolute;
    left: 40px; top: 0; width: 240px; height: 100%;
    display: flex; flex-direction: column; align-items: center; justify-content: center; gap: 14px;
  }
  .brand-block .mark-circle {
    width: 78px; height: 78px; border-radius: 50%;
    border: 3px solid var(--gold);
  }
  .brand-block .brand-name {
    color: var(--gold); font-size: 40px; font-weight: 400; letter-spacing: 1px; line-height: 1;
  }
  .divider {
    position: absolute; left: 300px; top: 58px;
    width: 2px; height: 190px; background: var(--gold);
  }
  .contact {
    position: absolute; left: 322px; top: 62px;
    color: var(--white); font-size: 15px; line-height: 1.25;
  }
  .contact .person-name { color: var(--gold); font-size: 21px; font-weight: 600; }
  .contact .role { margin-bottom: 8px; }
  .contact .company { color: var(--gold); font-weight: 600; font-size: 16px; }
  .contact .address { margin-bottom: 8px; }
  .contact-line { display: flex; align-items: center; gap: 8px; }
  .contact-line svg { width: 13px; height: 13px; flex: none; fill: var(--gold); stroke: var(--gold); }
</style>
</head>
<body>
  <section class="card card--front" aria-label="Card front">
    <div class="front-mark">
      <span class="mark-circle"></span>
      <span class="brand-name">LORVANTI</span>
    </div>
  </section>

  <section class="card card--back" aria-label="Card back">
    <div class="brand-block">
      <span class="mark-circle"></span>
      <span class="brand-name">LORVANTI</span>
    </div>
    <div class="divider"></div>
    <div class="contact">
      <div class="person-name">Dario Lorvanti</div>
      <div class="role">CEO and CO Founder</div>
      <div class="company">LORVANTI-Italy</div>
      <div class="address">4817 E Halvern</div>
      <div class="contact-line">
        <svg viewBox="0 0 16 16" aria-hidden="true"><path stroke="none" d="M3 1l3 3-2 2c1 2 3 4 5 5l2-2 3 3-2 3C7 15 1 9 1 3z"/></svg>
        <span>555-384-1926</span>
      </div>
      <div class="contact-line">
        <svg viewBox="0 0 16 16" aria-hidden="true"><path stroke="none" d="M4 1h7v4H4zM1 6h14v7h-3v2H4v-2H1zM5 11v3h6v-3z"/></svg>
        <span>555-384-1926</span>
      </div>
      <div class="contact-line">
        <svg viewBox="0 0 16 16" aria-hidden="true"><path stroke="none" d="M1 3h14v10H1zM2 4l6 5 6-5v1L8 10 2 5z" fill-rule="evenodd"/></svg>
        <span>dario@lorvanti.com</span>
      </div>
      <div class="contact-line">
        <svg viewBox="0 0 16 16" aria-hidden="true"><g fill="none" stroke-width="1.3"><circle cx="8" cy="8" r="6.5"/><ellipse cx="8" cy="8" rx="3" ry="6.5"/><path d="M1.5 8h13M3 4.5h10M3 11.5h10"/></g></svg>
        <span>LORVANTI.COM</span>
      </div>
    </div>
  </section>
</body>
</html>
```